Business Card Design - Photographer

I am a landscape photographer and I require a business card design. 

I require two designs:
1)  a double sided business card
 and
b)  a single sided business card 

The single sided design can either be the same as the double sided (with just one side having all the information)....or it can be an entire new design. Its up to you.

My corporate colours are (CMYK):

Blue   69, 32, 0, 0
Grey  72,  64,  47,  31
Green  32,  2,  91,  0
Yellow   0, 19, 92, 0
Orange  0, 39, 75, 0

Colour space in final file should be in CMYK.

The details that need to be included on the card:

- Use the provided Logo
- Name: Wiktor Baranowski
- Email:   sales@vistalumeworks.com.au
- Website:    vistalumeworks.com.au
- Twitter:    twitter.com/vistalumeworks
- Facebook:   facebook.com/vistalumeworks
- Mobile  0417 539 662

Please use the attached template to design the logo to the specified size, including the marked bleed lines. I have also attached my logo in PNG (transparent background) and ai format for you to use.

The final file should be:
- Photoshop version with layers so I can edit the name/text etc. All non vector files should be high resolution at 1039 x 697 pixels at 300 dpi.

I also require a file as:
- Vector based PDF

Anyway questions please contact me.

Thank you

Industry/Entity Type

Landscape

Logo styles of interest
Pictorial/Combination Logo
Abstract Logo
Wordmark Logo
Lettermark Logo
Requirements
Must have
• The details that need to be included on the card:

- Use the provided Logo
- Name: Wiktor Baranowski
- Email: sales@vistalumeworks.com.au
- Website: vistalumeworks.com.au
- Twitter: twitter.com/vistalumeworks
- Facebook: facebook.com/vistalumeworks
- Mobile 0417 539 662

```html
<!DOCTYPE html>
<html lang="en">
<head>
<meta charset="utf-8">
<title>Vistalume Works – Business Card</title>
<link rel="stylesheet" href="https://fonts.googleapis.com/css2?family=Cinzel:wght@500&family=Open+Sans:wght@400;700&display=swap">
<style>
  :root {
    --page-bg: #2b2e33;
    --slate: #3d3f50;
    --paper: #ffffff;
    --ink: #3b3d4c;
    --text-grey: #3a3a3a;
    --rule-grey: #8a8a8a;
  }
  * { margin: 0; padding: 0; box-sizing: border-box; }
  html, body { width: 987px; height: 1200px; overflow: hidden; }
  body {
    background: var(--page-bg);
    position: relative;
    font-family: "Open Sans", Arial, sans-serif;
  }
  .card {
    position: absolute;
    width: 790px;
    height: 450px;
    border-radius: 28px;
    overflow: hidden;
  }
  .card--front { left: 100px; top: 85px; background: var(--paper); }
  .card--back { left: 92px; top: 637px; background: var(--slate); }

  .front-swoosh { position: absolute; left: 0; top: 0; }

  .brand-mark {
    position: absolute;
    border-radius: 50%;
  }
  .card--front .brand-mark {
    left: 200px; top: 23px; width: 160px; height: 160px;
    background: var(--ink);
  }
  .card--back .brand-mark {
    left: 288px; top: 30px; width: 210px; height: 210px;
    background: var(--paper);
  }

  .brand-name {
    position: absolute;
    font-family: "Cinzel", "Times New Roman", serif;
    font-weight: 500;
    white-space: nowrap;
    text-align: center;
    letter-spacing: 1px;
  }
  .card--front .brand-name {
    left: 40px; width: 480px; top: 196px;
    font-size: 45px; color: var(--ink);
  }
  .card--back .brand-name {
    left: 45px; width: 700px; top: 254px;
    font-size: 60px; color: var(--paper);
  }

  .person {
    position: absolute;
    right: 538px; top: 342px;
    text-align: right;
    color: var(--text-grey);
  }
  .person__name { font-size: 29px; font-weight: 700; line-height: 1.1; }
  .person__role { font-size: 18px; line-height: 1.5; }

  .contact-divider {
    position: absolute;
    left: 273px; top: 313px;
    width: 1px; height: 110px;
    background: var(--rule-grey);
  }
  .contact-list {
    position: absolute;
    left: 288px; top: 306px;
    list-style: none;
    font-size: 17px;
    line-height: 24.4px;
    white-space: nowrap;
    color: var(--text-grey);
  }
  .contact-list b { font-weight: 700; }

  .back-web {
    position: absolute;
    left: 0; width: 790px; top: 396px;
    text-align: center;
    font-size: 25px;
    color: var(--paper);
  }
</style>
</head>
<body>
  <section class="card card--front">
    <svg class="front-swoosh" width="790" height="450" viewBox="0 0 790 450" aria-hidden="true">
      <rect width="790" height="450" fill="var(--slate)"/>
      <path d="M0,0 H545 C710,60 800,300 665,450 H0 Z" fill="var(--paper)"/>
      <path d="M615,0 H648 C800,110 800,300 705,385 C760,290 745,110 615,0 Z" fill="var(--paper)"/>
    </svg>
    <div class="brand-mark"></div>
    <div class="brand-name">VISTALUME WORKS</div>
    <div class="person">
      <div class="person__name">Your Name</div>
      <div class="person__role">Adminsitrator</div>
    </div>
    <div class="contact-divider"></div>
    <ul class="contact-list">
      <li><b>m</b> : 0417 539 662</li>
      <li><b>e</b> : sales@vistalumeworks.com.au</li>
      <li><b>w</b> : vistalumeworks.com.au</li>
      <li><b>t</b> : chirpline.com/vistalumeworks</li>
      <li><b>f</b> : friendsquare.com/vistalumeworks</li>
    </ul>
  </section>

  <section class="card card--back">
    <div class="brand-mark"></div>
    <div class="brand-name">VISTALUME WORKS</div>
    <div class="back-web">www.vistalumeworks.com.au</div>
  </section>
</body>
</html>
```